Audit/Compliance company needs Business Card Template

We are after a Business Card Template that we can modify internally to update details as people change positions.
We are an Australian based company specalising in Auditing and Quality/OHS systems development. - See www.brimfieldreview.com.au for more information
We would like the desings to be based around our logo and colours assocaited with it (attached for your information) however we are very open as to how the cards are designed.
We are looking for something quite edgy and mordern but it must have a professional/compliance feel to it (if possible).
The main details we would like to include within the card template are:
Name
Position Title
Postal Address
Phone Number
Mobile Number
Email Address
Website
The cards will be printed through lanterly press on Glossy paper so it should reflect the requirements below
Full Bleed Size (starting document size)
90 x 52 mm
1062 x 615 pixels
Document Trim Size (final size after being cut)
87 x 49 mm
1028 x 579 pixels
Resolution
300 DPI

```html
<!DOCTYPE html>
<html lang="en">
<head>
<meta charset="utf-8">
<title>Brimfield Review &amp; Compliance – Business Card</title>
<link rel="stylesheet" href="https://fonts.googleapis.com/css2?family=Cabin:wght@400;500&display=swap">
<style>
  :root {
    --navy-deep: #0e1628;
    --navy: #16203a;
    --cyan: #1ea7d9;
    --white: #ffffff;
    --ink: #3d3d3f;
    --paper-light: #fbfbfc;
    --paper-edge: #e6e7e9;
    --frame: #8a8a8a;
    --rule: #6f6f72;
    --brand-mark: #f39a1e;
  }
  * { box-sizing: border-box; margin: 0; padding: 0; }
  html, body {
    width: 940px;
    height: 1200px;
    overflow: hidden;
    background: var(--white);
    font-family: "Cabin", sans-serif;
  }
  .canvas { position: relative; width: 940px; height: 1200px; }

  .card {
    position: absolute;
    left: 14px;
    width: 912px;
    height: 526px;
    overflow: hidden;
  }

  /* Front */
  .card-front {
    top: 53px;
    background: linear-gradient(90deg, var(--navy) 0%, var(--navy-deep) 100%);
  }
  .card-front .edge-glow {
    position: absolute;
    left: 0; top: 0; bottom: 0;
    width: 64px;
    background: linear-gradient(90deg, var(--cyan) 0%, rgba(30,167,217,0.35) 45%, rgba(30,167,217,0) 100%);
  }
  .brand-tab {
    position: absolute;
    left: 0;
    top: 182px;
    width: 494px;
    height: 154px;
    background: var(--white);
    border-radius: 0 30px 30px 0;
    display: flex;
    align-items: center;
    padding-left: 46px;
    gap: 16px;
  }
  .brand-mark {
    width: 22px;
    height: 22px;
    background: var(--brand-mark);
    flex: none;
  }
  .brand-name {
    font-size: 23px;
    font-weight: 500;
    color: var(--navy);
    letter-spacing: 0.5px;
    line-height: 1.25;
    text-transform: uppercase;
  }
  .chevron { position: absolute; inset: 0; }
  .holder {
    position: absolute;
    left: 709px;
    transform: translateX(-50%);
    text-align: center;
    color: var(--white);
    white-space: nowrap;
  }
  .holder-name { top: 220px; font-size: 29px; font-weight: 500; }
  .holder-role { top: 270px; font-size: 22px; font-weight: 500; }

  /* Back */
  .card-back {
    top: 607px;
    height: 527px;
    border: 1px solid var(--frame);
    background: radial-gradient(ellipse at 50% 45%, var(--paper-light) 0%, #f2f3f4 55%, var(--paper-edge) 100%);
    color: var(--ink);
  }
  .phones {
    position: absolute;
    right: 12px;
    top: 14px;
    text-align: right;
    font-size: 24px;
    line-height: 32px;
  }
  .contact {
    position: absolute;
    left: 0; right: 0;
    text-align: center;
    font-size: 24px;
  }
  .contact-email { top: 156px; }
  .contact-web { top: 250px; }
  .contact-address { top: 340px; font-size: 25px; }
  .divider {
    position: absolute;
    left: 228px;
    width: 430px;
    height: 2px;
    background: linear-gradient(90deg, rgba(111,111,114,0.3), var(--rule) 30%, var(--rule) 70%, rgba(111,111,114,0.3));
  }
  .divider-one { top: 214px; }
  .divider-two { top: 307px; }
</style>
</head>
<body>
<main class="canvas">
  <section class="card card-front" aria-label="Card front">
    <div class="edge-glow"></div>
    <div class="brand-tab">
      <span class="brand-mark" aria-hidden="true"></span>
      <span class="brand-name">Brimfield Review<br>&amp; Compliance</span>
    </div>
    <svg class="chevron" width="912" height="526" viewBox="0 0 912 526" aria-hidden="true">
      <polyline points="773,36 544,253 759,483" fill="none" stroke="#ffffff" stroke-width="1.4"/>
    </svg>
    <p class="holder holder-name">Dara Whitlow</p>
    <p class="holder holder-role">Manager</p>
  </section>

  <section class="card card-back" aria-label="Card back">
    <div class="phones">
      <p>Phone number</p>
      <p>Mobile number</p>
    </div>
    <p class="contact contact-email">email@email.com</p>
    <div class="divider divider-one"></div>
    <p class="contact contact-web">www.brimfieldreview.com.au</p>
    <div class="divider divider-two"></div>
    <p class="contact contact-address">Unit 48, Harbour Row, Sydney, Australia</p>
  </section>
</main>
</body>
</html>
```